Trifold - Brandt Commercial Roofing

Enhance the look, change the images if needed. Create some interest please!

Target Market(s)

Commercial and Industrial Building Owners

Industry/Entity Type

Roofing

Font styles to use
Serif

Requirements
Must have
• Organized layout, call to action

```html
<!DOCTYPE html>
<html lang="en">
<head>
<meta charset="utf-8">
<title>Brandt Commercial Roofing – Trifold</title>
<link rel="stylesheet" href="https://fonts.googleapis.com/css2?family=Montserrat:wght@400;500;600;700&family=Open+Sans:wght@400;600;700&display=swap">
<style>
:root{
  --orange:#f26a21;
  --ink:#1d1d1d;
  --black:#141414;
  --paper:#ffffff;
  --stage:#e6e6e6;
  --grey:#555;
  --head:'Montserrat',sans-serif;
  --body:'Open Sans',sans-serif;
}
*{box-sizing:border-box;margin:0;padding:0}
html,body{width:1200px;height:3000px;overflow:hidden;background:var(--stage)}
body{font-family:var(--body);color:var(--ink)}
.spread{position:absolute;left:50px;width:1100px;height:850px;background:var(--paper);display:grid;grid-template-columns:repeat(3,1fr);box-shadow:0 10px 30px rgba(0,0,0,.18);overflow:hidden}
.spread--outside{top:120px}
.spread--inside{top:1080px}
.panel{position:relative;padding:0 30px;height:100%}

/* outside */
.founder-photo{height:370px;margin:0 -30px;background:linear-gradient(160deg,#5a3a2a 0%,#2b1d17 45%,#c9a46a 100%)}
.founder-title{font-family:var(--head);color:var(--orange);font-weight:700;font-size:20px;margin-top:26px}
.founder-role{font-size:12px;line-height:1.4;margin-bottom:18px}
.copy{font-size:12.5px;line-height:1.5;text-align:justify;margin-bottom:16px}
.mission-title{font-family:var(--head);font-weight:500;font-size:34px;line-height:1.05;text-align:center;margin-top:30px}
.mission-lead{font-size:12.5px;line-height:1.45;text-align:center;margin:14px 0 10px}
.charity{display:grid;grid-template-columns:22px 1fr;gap:8px;margin-top:16px}
.dot{width:16px;height:16px;border:2px solid var(--ink);border-radius:50%;margin-top:3px}
.charity h3{font-family:var(--head);color:var(--orange);font-size:16px;font-weight:600}
.charity h4{font-size:13px;font-weight:700;margin:6px 0 2px}
.charity p{font-size:12px;line-height:1.35}
.footer-band{position:absolute;left:366.67px;right:0;bottom:0;height:265px;background:var(--black)}
.contact{position:absolute;left:0;right:0;bottom:0;height:265px;color:#fff;text-align:center;padding-top:32px;font-size:12px;line-height:1.5}
.brand{font-family:var(--head);font-weight:600;letter-spacing:.28em;text-transform:uppercase;color:var(--ink)}
.contact .brand{color:#fff;font-size:15px}
.contact .phone{font-weight:700;font-size:14px;margin-top:18px}
.contact svg{display:block;margin:10px auto 4px}
.cover .brand{display:block;text-align:center;font-size:24px;line-height:1.35;margin-top:40px}
.cover-photo{position:relative;z-index:2;margin:28px auto 0;width:306px;height:445px;border:6px solid #fff;box-shadow:0 4px 12px rgba(0,0,0,.3);background:linear-gradient(180deg,#3f7fd0 0%,#8fb8e6 30%,#d9d4c8 55%,#6f8a4a 80%,#4d6b35 100%)}
.cover-tag{position:relative;z-index:2;color:#fff;text-align:center;font-family:var(--head);font-weight:700;font-size:25px;line-height:1.05;margin-top:30px}
.cover-web{position:relative;z-index:2;color:#fff;text-align:center;font-size:19px;margin-top:18px}

/* inside */
.section-head{display:flex;align-items:center;gap:12px;margin-top:40px}
.section-head .dot{width:22px;height:22px;margin:0}
.section-head h2{font-family:var(--head);color:var(--orange);font-size:34px;font-weight:600}
.ticks{list-style:none;margin-top:18px}
.ticks li{display:flex;gap:8px;align-items:center;font-size:11.5px;margin-bottom:14px}
.ticks svg{flex:none}
.photo{background:linear-gradient(180deg,#a9c6e6,#e7e3da 55%,#8a8a7a)}
.photo--office{height:150px;margin:20px 0}
.photo--campus{height:185px;margin:10px 0;background:linear-gradient(180deg,#6c9bd4,#b27a55 55%,#5c5a55)}
.photo--flood{width:150px;height:150px;background:linear-gradient(160deg,#8d9a98,#cdd3cf 60%,#6f7a74)}
.photo--fire{height:205px;margin:18px 0 22px;background:linear-gradient(160deg,#2c2f38 0%,#4b4f5a 40%,#e0702a 60%,#3a3d46 100%)}
.restore-top{display:flex;gap:12px}
.skyline{position:absolute;left:0;right:0;bottom:0;height:130px;background:linear-gradient(180deg,rgba(20,20,20,0) 0%,var(--black) 45%)}
</style>
</head>
<body>

<section class="spread spread--outside">
  <div class="footer-band"></div>

  <article class="panel">
    <div class="founder-photo" role="img" aria-label="Portrait of the company founder seated in a carved wooden chair"></div>
    <h2 class="founder-title">Founder &amp; Priciple</h2>
    <p class="founder-role">Morgan Hale, nationally accredited interior designer and builder.</p>
    <p class="copy">Brandt Commercial is a woman-owned business serving the roofing and construction industry. With more than 15 years of experience and strategic partnerships it is our goal to share our industry knowledge and expertise to build and maintain the systems that protect your assets.</p>
    <p class="copy">We strive to build quality structures and devise the best roofing solution for your requirements and budget. Clients receive the utmost attention to detail in understanding the work scope and expectations of a project from beginning to end. We are committed to quality installation processes and providing safe work environments for our skilled trades men and women.</p>
  </article>

  <article class="panel">
    <h1 class="mission-title">FAITH BASED<br>MISSION MINDED</h1>
    <p class="mission-lead">10% of all Brandt Commercial proceeds support our mission to restore hope and inspire change into the lives of those who we are all connected.<br><br>Sign with Brandt Commercial and select one of our sponsored charities:</p>
    <div class="charity"><span class="dot"></span><div><h3>Clearwell Relief International</h3><h4>Clean Water Efforts</h4><p>Bring clean water wells, sanitation, &amp; hygiene to communities in need.</p></div></div>
    <div class="charity"><span class="dot"></span><div><h3>Harbor Life Center</h3><h4>Local and World Missionaries</h4><p>Rebuild and restore, food shortage aid and community outreach.</p></div></div>
    <div class="charity"><span class="dot"></span><div><h3>Safe Haven Alliance</h3><h4>End Child Sex Trafficking</h4><p>Bring an end to sex trafficking through prevention, restoration, and justice.</p></div></div>
    <div class="contact">
      <span class="brand">Brandt<br>Commercial</span>
      <p class="phone">312-555-0148</p>
      <svg width="14" height="18" viewBox="0 0 14 18" aria-hidden="true"><path d="M7 1a6 6 0 0 0-6 6c0 4.5 6 10 6 10s6-5.5 6-10a6 6 0 0 0-6-6z" fill="#fff"/><circle cx="7" cy="7" r="2.2" fill="#141414"/></svg>
      <p>4410 Harlow Street, Suite B<br>Westbrook, IL 60500</p>
      <p style="margin-top:12px">www.brandtroof.com</p>
    </div>
  </article>

  <article class="panel cover">
    <span class="brand">Brandt<br>Commercial</span>
    <div class="cover-photo" role="img" aria-label="Aerial view of a large commercial building complex under blue sky"></div>
    <p class="cover-tag">KNOWLEDGEABLE<br>TRUSTWORTHY<br>COMMITTED</p>
    <p class="cover-web">www.brandtroof.com</p>
  </article>
</section>

<svg width="0" height="0" style="position:absolute">
  <defs>
    <symbol id="tick" viewBox="0 0 12 12"><path d="M1.5 6.5l3 3 6-7" fill="none" stroke="#f26a21" stroke-width="2" stroke-linecap="round" stroke-linejoin="round"/></symbol>
  </defs>
</svg>

<section class="spread spread--inside">
  <article class="panel">
    <div class="section-head"><span class="dot"></span><h2>Roofing</h2></div>
    <ul class="ticks">
      <li><svg width="12" height="12"><use href="#tick"/></svg>New Construction</li>
      <li><svg width="12" height="12"><use href="#tick"/></svg>Tear off and Replacement</li>
      <li><svg width="12" height="12"><use href="#tick"/></svg>Vented Full Overlay</li>
      <li><svg width="12" height="12"><use href="#tick"/></svg>Preventative Maintenance</li>
      <li><svg width="12" height="12"><use href="#tick"/></svg>Inspections</li>
    </ul>
    <p class="copy">Our free roof evaluation will offer you insight to determine whether you are in need of a routine maintenance plan or if the roof is due for repairs, vented overlay or a full replacement.</p>
    <div class="photo photo--office" role="img" aria-label="Modern two-storey commercial office building"></div>
    <ul class="ticks">
      <li><svg width="12" height="12"><use href="#tick"/></svg>Flat Roof: EPDM, Modified Bitumen, TPO</li>
      <li><svg width="12" height="12"><use href="#tick"/></svg>Metal Roof: Standing Seam</li>
      <li><svg width="12" height="12"><use href="#tick"/></svg>Shingles: Standard + Steep Slope Structures</li>
      <li><svg width="12" height="12"><use href="#tick"/></svg>Glass Atriums + Skylights</li>
      <li><svg width="12" height="12"><use href="#tick"/></svg>Eco Roofing + Green Roofing</li>
    </ul>
  </article>

  <article class="panel">
    <div class="section-head"><span class="dot"></span><h2>Construction</h2></div>
    <ul class="ticks">
      <li><svg width="12" height="12"><use href="#tick"/></svg>New Construction 5,000sf +</li>
      <li><svg width="12" height="12"><use href="#tick"/></svg>Full Gut Renovation</li>
      <li><svg width="12" height="12"><use href="#tick"/></svg>Carpentry</li>
      <li><svg width="12" height="12"><use href="#tick"/></svg>HVAC / Plumbing / Electrical</li>
      <li><svg width="12" height="12"><use href="#tick"/></svg>Fire Alarm Systems &amp; Testing</li>
      <li><svg width="12" height="12"><use href="#tick"/></svg>City Storm Water</li>
      <li><svg width="12" height="12"><use href="#tick"/></svg>10,000 ~ 300,000 SF structures</li>
      <li><svg width="12" height="12"><use href="#tick"/></svg>State and Local Contracts</li>
      <li><svg width="12" height="12"><use href="#tick"/></svg>Government and Municiple Bidding</li>
      <li><svg width="12" height="12"><use href="#tick"/></svg>Architectural + Engineering Drawing</li>
      <li><svg width="12" height="12"><use href="#tick"/></svg>Commercial Real Estate</li>
    </ul>
    <div class="photo photo--campus" role="img" aria-label="Brick commercial building with parking lot"></div>
  </article>

  <article class="panel">
    <div class="section-head"><span class="dot"></span><h2>Restoration</h2></div>
    <div class="restore-top">
      <ul class="ticks">
        <li><svg width="12" height="12"><use href="#tick"/></svg>Fire Restoration</li>
        <li><svg width="12" height="12"><use href="#tick"/></svg>Smoke Restoration</li>
        <li><svg width="12" height="12"><use href="#tick"/></svg>Flood Restoration</li>
        <li><svg width="12" height="12"><use href="#tick"/></svg>Mold Remediation</li>
        <li><svg width="12" height="12"><use href="#tick"/></svg>Storm Restoration</li>
      </ul>
      <div class="photo photo--flood" role="img" aria-label="Flooded commercial interior"></div>
    </div>
    <div class="photo photo--fire" role="img" aria-label="Commercial building on fire with heavy smoke"></div>
    <p class="copy">Has your property suffered from a fire or natural disaster? Allow us to pick up the pieces from clean up to rebuild. We work with your insurance company to alleviate the burden by sending an expert team to overcome the damages. It is our priority to restore your property and get you back to business.</p>
  </article>

  <div class="skyline" role="img" aria-label="City skyline silhouette along the bottom edge"></div>
</section>

</body>
</html>
```